Wedding Invitations

We are a printing company "inkhollow" and require multiple wedding invitation designs for our customers in store and online. We would like the designs to be editable in Photoshop if possible, if not then a layout with suggested fonts would be the next best option. We are open to suggestions on design but would like to stick to the general wedding themes some with a modern and some with a classical feel

Industry/Entity Type

Printing

```html
<!DOCTYPE html>
<html lang="en">
<head>
<meta charset="utf-8">
<title>Wedding Invitation — inkhollow</title>
<link rel="stylesheet" href="https://fonts.googleapis.com/css2?family=Tinos&family=Parisienne&display=swap">
<style>
  :root {
    --cream: #efead2;
    --olive: #6b5a22;
    --olive-text: #6e5e24;
    --rose: #d46a6a;
    --rose-soft: #e29a92;
  }
  html, body {
    margin: 0;
    padding: 0;
    overflow: hidden;
    background: var(--cream);
  }
  .invitation {
    position: relative;
    width: 1200px;
    height: 848px;
    background: var(--cream);
    overflow: hidden;
    font-family: "Tinos", "Times New Roman", serif;
    color: var(--olive-text);
  }
  .side-band {
    position: absolute;
    left: 0;
    top: 0;
    width: 74px;
    height: 848px;
    background: var(--olive);
  }
  .side-rule {
    position: absolute;
    left: 79px;
    top: 0;
    width: 8px;
    height: 848px;
    background: var(--olive);
  }
  .band-ornament {
    position: absolute;
    left: 8px;
    top: 72px;
    width: 56px;
    height: 46px;
    border-radius: 50% 50% 40% 40%;
    background: radial-gradient(ellipse at 50% 60%, #e8e0bf 0%, #c9bd8c 70%, rgba(201,189,140,0) 100%);
  }
  .floral-art {
    position: absolute;
    left: 716px;
    top: 128px;
    width: 484px;
    height: 720px;
    border-top-left-radius: 70% 60%;
    background:
      radial-gradient(ellipse at 52% 28%, rgba(212,106,106,0.55) 0%, rgba(212,106,106,0) 38%),
      radial-gradient(ellipse at 20% 85%, rgba(212,106,106,0.45) 0%, rgba(212,106,106,0) 30%),
      linear-gradient(160deg, rgba(239,234,210,0) 0%, rgba(226,154,146,0.35) 45%, rgba(107,90,34,0.35) 100%);
  }
  .line {
    position: absolute;
    left: 431px;
    transform: translateX(-50%);
    margin: 0;
    white-space: nowrap;
    font-size: 22px;
    letter-spacing: 0.3px;
    line-height: 1;
  }
  .families { top: 62px; }
  .invite-1 { top: 259px; }
  .invite-2 { top: 301px; }
  .date-1 { top: 403px; }
  .date-2 { top: 442px; }
  .time { top: 485px; }
  .venue { top: 583px; }
  .city { top: 616px; }
  .names {
    position: absolute;
    margin: 0;
    font-family: "Parisienne", cursive;
    font-weight: 400;
    line-height: 1;
    white-space: nowrap;
  }
  .name-bride { left: 219px; top: 100px; font-size: 66px; color: var(--rose); }
  .name-and { left: 370px; top: 160px; font-size: 36px; color: var(--olive); }
  .name-groom { left: 465px; top: 152px; font-size: 66px; color: var(--rose); }
  .rsvp {
    position: absolute;
    left: 99px;
    top: 756px;
    margin: 0;
    font-size: 17px;
    line-height: 22px;
    letter-spacing: 0.4px;
  }
</style>
</head>
<body>
<main class="invitation">
  <div class="side-band">
    <div class="band-ornament" role="img" aria-label="Small cream lotus leaf ornament"></div>
  </div>
  <div class="side-rule"></div>

  <div class="floral-art" role="img" aria-label="Illustration of pink lotus flowers on curving olive stems and leaves"></div>

  <p class="line families">TOGTHER WITH THEIR FAMILIES</p>

  <h1 class="names name-bride">Bride</h1>
  <span class="names name-and">and</span>
  <span class="names name-groom">Bride groom</span>

  <p class="line invite-1">INVITE YOU TO SHARE IN THEIR</p>
  <p class="line invite-2">WEDDING CELEBRATION</p>

  <p class="line date-1">SATURDAY,THE TWENTY-SECOND OF DECEMBER</p>
  <p class="line date-2">TWO THOUSAND AND FOURTEEN</p>
  <p class="line time">TWO O’CLOCK THE AFTHERNOON</p>

  <p class="line venue">ANYWHERE HOTEL</p>
  <p class="line city">CITY, STATE</p>

  <p class="rsvp">RSVP<br>by date<br>phone number</p>
</main>
</body>
</html>
```